Business Cards for a law firm

Business cards for our law firm. Use our silhoette logo and OAK PARTNERS - check our website (www.oakpartners.example)

Contact Information for Business Card

our silhouette logo, OAK PARTNERS, 800-555-0147, Dorian Pemberton, dorian@oakpartners.example

Requirements
Must have
• our silhouette logo, OAK PARTNERS, 800-555-0147, Dorian Pemberton, dorian@oakpartners.example

```html
<!DOCTYPE html>
<html lang="en">
<head>
<meta charset="utf-8">
<title>Oak Partners — Business Cards</title>
<link href="https://fonts.googleapis.com/css2?family=Cinzel:wght@600;700&family=Arimo:wght@400&display=swap" rel="stylesheet">
<style>
  :root {
    --navy: #1a2f6b;
    --navy-soft: #2a4184;
    --orange: #f0a01e;
    --white: #ffffff;
    --ink: #3a3a3a;
    --backdrop: #e9e9ec;
  }
  html, body {
    margin: 0;
    width: 1200px;
    height: 874px;
    overflow: hidden;
    background: var(--backdrop);
  }
  .sheet {
    position: relative;
    width: 1200px;
    height: 874px;
  }
  .card {
    position: absolute;
    left: 320px;
    width: 560px;
    height: 320px;
    border-radius: 22px;
    overflow: hidden;
    box-shadow: 0 6px 18px rgba(0,0,0,0.18);
  }
  .card--back {
    top: 97px;
    background: var(--navy);
    display: flex;
    align-items: center;
    justify-content: center;
  }
  .card--front {
    top: 457px;
    background: var(--white);
  }
  .wordmark {
    font-family: "Cinzel", serif;
    font-weight: 700;
    letter-spacing: 0.08em;
    margin: 0;
  }
  .card--back .wordmark {
    color: var(--white);
    font-size: 34px;
  }
  .card--front .wordmark {
    position: absolute;
    left: 34px;
    top: 30px;
    color: var(--navy);
    font-size: 26px;
  }
  .holder {
    position: absolute;
    left: 34px;
    top: 120px;
  }
  .holder__name {
    font-family: "Cinzel", serif;
    font-weight: 700;
    font-size: 20px;
    letter-spacing: 0.04em;
    color: var(--navy);
    margin: 0;
  }
  .holder__rule {
    width: 24px;
    height: 2px;
    background: var(--orange);
    margin: 8px 0 12px;
  }
  .contact {
    list-style: none;
    margin: 0;
    padding: 0;
    font-family: "Arimo", sans-serif;
    font-size: 14px;
    color: var(--ink);
  }
  .contact li {
    display: flex;
    align-items: center;
    gap: 9px;
    line-height: 20px;
  }
  .contact svg {
    width: 12px;
    height: 12px;
    flex: none;
  }
  .portrait-area {
    position: absolute;
    left: 330px;
    top: 70px;
    width: 190px;
    height: 225px;
    border-radius: 60px 60px 8px 8px;
    background: linear-gradient(180deg, var(--navy-soft), var(--navy));
  }
  .ground {
    position: absolute;
    left: 0;
    bottom: 0;
    width: 560px;
    height: 110px;
  }
</style>
</head>
<body>
<main class="sheet">
  <section class="card card--back">
    <h1 class="wordmark">OAK PARTNERS</h1>
  </section>

  <section class="card card--front">
    <svg class="ground" viewBox="0 0 560 110" preserveAspectRatio="none" aria-hidden="true">
      <path d="M150 110 C 280 30, 440 20, 560 60 L 560 110 Z" fill="var(--orange)"/>
    </svg>
    <div class="portrait-area" role="img" aria-label="Silhouettes of two standing men in suits"></div>

    <h2 class="wordmark">OAK PARTNERS</h2>

    <div class="holder">
      <p class="holder__name">Dorian Pemberton</p>
      <div class="holder__rule"></div>
      <ul class="contact">
        <li>
          <svg viewBox="0 0 12 12" aria-hidden="true"><path d="M2.5 1 L4.5 1 L5.2 3.6 L4 4.6 C4.6 6 6 7.4 7.4 8 L8.4 6.8 L11 7.5 L11 9.5 C11 10.4 10.3 11 9.5 11 C5 10.7 1.3 7 1 2.5 C1 1.7 1.6 1 2.5 1 Z" fill="var(--orange)"/></svg>
          800-555-0147
        </li>
        <li>
          <svg viewBox="0 0 12 12" aria-hidden="true"><rect x="0.5" y="2" width="11" height="8" fill="var(--orange)"/><path d="M0.5 2 L6 6.5 L11.5 2" fill="none" stroke="var(--white)" stroke-width="1"/></svg>
          dorian@oakpartners.example
        </li>
        <li>
          <svg viewBox="0 0 12 12" aria-hidden="true"><circle cx="6" cy="6" r="5.5" fill="var(--orange)"/><path d="M0.5 6 H11.5 M6 0.5 C3.5 3 3.5 9 6 11.5 M6 0.5 C8.5 3 8.5 9 6 11.5" fill="none" stroke="var(--white)" stroke-width="0.8"/></svg>
          www.oakpartners.example
        </li>
      </ul>
    </div>
  </section>
</main>
</body>
</html>
```